Brightline Energy Product Distribution Brochure

We are looking to have our current brochure for our customers completely redesigned...the idea is to present the relevant information in an attractive way . Our website is brightlineenergyco.example where you can find more information about us. We have included a file with a rough idea of the page order and what each should include but feel free to adapt based on design. The example provided is only for context and doesnt have to be maintained. We will be using the brochure both digitally and in print form. As long as it reads easily and is eye catching, the design can be horizontal or vertical.Final deliverable should be indesign file.

"Our Brands" page: should be limited to one page (space being enough) where it has the header for each one (for example diesel generators) space for one or two lines of text and then the corresponding logos for each of the five categories
Updates

For those asking: the "our brands" page should be a single page layout where there is a header with the corresponding section and space for maybe one line of text followed by the two logos for that category. Each of the product pages should be similar in fashion to the one in the document attached: a photo of the product with some white space and space for the text to be included. We will be posting additional examples today

Target Market(s)

We want to present it to customers both digitally and in print so they can see our products

Industry/Entity Type

Power Generation

Font styles to use
Serif

Requirements
Must have
• Eye catching and able to present the information in a presentable fashion. Rest is up to you.
Nice to have
• Should incorporate the colors of our logo but can also add other depending on design

```html
<!DOCTYPE html>
<html lang="en">
<head>
<meta charset="utf-8">
<title>Brightline Energy – Our Stock</title>
<link rel="stylesheet" href="https://fonts.googleapis.com/css2?family=Montserrat:wght@500;700&family=Raleway:wght@300&family=Source+Serif+4:opsz,wght@8..60,400&display=swap">
<style>
  :root {
    --backdrop: #e8e8e9;
    --paper: #f3f3f3;
    --yellow: #f1c21b;
    --yellow-light: #f5cf3c;
    --charcoal: #4a4849;
    --charcoal-light: #555354;
    --ring-grey: #e2e2e2;
    --photo-light: #f4f4f4;
    --photo-mid: #dedede;
    --ink: #3b3b3b;
    --ink-soft: #6b6b6b;
    --folio: #cfcfcf;
  }
  * { box-sizing: border-box; margin: 0; padding: 0; }
  html, body { width: 1200px; height: 453px; overflow: hidden; background: var(--backdrop); }
  .canvas { position: relative; width: 1200px; height: 453px; }

  .spread { position: absolute; top: 36px; display: flex; width: 526px; height: 380px; }
  .spread--left { left: 46px; }
  .spread--right { left: 628px; }

  .page { position: relative; width: 263px; height: 380px; background: var(--paper); overflow: hidden; }

  .halo { position: absolute; left: 0; top: 0; width: 263px; height: 380px; }
  .band-yellow { position: absolute; left: 0; right: 0; top: 204px; height: 80px; background: var(--yellow); }
  .band-dark { position: absolute; left: 0; right: 0; top: 284px; bottom: 0; background: var(--charcoal); }
  .medallion { position: absolute; left: 0; top: 0; width: 263px; height: 380px; }

  .product-photo {
    position: absolute; left: 73px; top: 218px; width: 116px; height: 116px; border-radius: 50%;
    background: radial-gradient(circle at 50% 45%, var(--photo-light) 0 55%, var(--photo-mid) 100%);
  }

  .gutter { position: absolute; top: 0; bottom: 0; width: 14px; pointer-events: none; }
  .page--verso .gutter { right: 0; background: linear-gradient(to left, rgba(0,0,0,.12), rgba(0,0,0,0)); }
  .page--recto .gutter { left: 0; background: linear-gradient(to right, rgba(0,0,0,.12), rgba(0,0,0,0)); }

  .running-head { position: absolute; top: 18px; left: 0; right: 0; height: 10px;
    font: 500 5.4px/10px "Montserrat", sans-serif; color: var(--ink-soft); letter-spacing: .2px; }
  .running-head .bar { position: absolute; top: 3px; width: 20px; height: 4px; background: var(--yellow); }
  .page--verso .running-head .bar { left: 0; }
  .page--verso .running-head .section { position: absolute; left: 24px; padding-left: 5px; border-left: 1px solid #bbb; }
  .page--recto .running-head .bar { right: 0; }
  .page--recto .running-head .section { position: absolute; right: 30px; }

  .brand-mark { position: absolute; top: 0; display: flex; align-items: center; gap: 3px;
    font: 700 5.4px/10px "Montserrat", sans-serif; color: var(--ink); text-transform: uppercase; }
  .brand-mark i { width: 6px; height: 6px; background: var(--yellow); display: block; }
  .page--verso .brand-mark { right: 18px; }
  .page--recto .brand-mark { left: 22px; }

  .title { position: absolute; left: 22px; top: 43px; font: 300 16.5px/1 "Raleway", sans-serif;
    color: var(--ink); letter-spacing: .2px; white-space: nowrap; }
  .subtitle { position: absolute; left: 22px; top: 75px; display: flex; align-items: center; gap: 3px;
    font: 700 7.2px/1 "Montserrat", sans-serif; color: var(--ink); white-space: nowrap; }
  .subtitle svg { width: 7px; height: 7px; }

  .intro { position: absolute; left: 22px; top: 89px; width: 108px;
    font: 400 4.6px/1.42 "Source Serif 4", Georgia, serif; color: var(--ink-soft); text-align: justify; }
  .points { position: absolute; left: 135px; top: 89px; width: 110px; list-style: none;
    font: 400 4.6px/1.42 "Source Serif 4", Georgia, serif; color: var(--ink-soft); }
  .points li { position: relative; padding-left: 10px; margin-bottom: 5px; }
  .points li span { position: absolute; left: 0; top: 0; width: 6px; height: 6px; background: var(--yellow);
    color: #fff; font: 700 4px/6px "Montserrat", sans-serif; text-align: center; }

  .feature-mark { position: absolute; right: 18px; top: 150px; display: flex; align-items: center; gap: 4px;
    font: 700 6.5px/1 "Montserrat", sans-serif; color: var(--ink); text-transform: uppercase; }
  .feature-mark i { width: 10px; height: 10px; background: var(--yellow); display: block; }

  .folio { position: absolute; bottom: 9px; font: 400 4.2px/1 "Montserrat", sans-serif; color: var(--folio);
    display: flex; align-items: center; gap: 5px; }
  .folio .rule { width: 18px; height: 1px; background: var(--yellow); }
  .page--verso .folio { left: 18px; }
  .page--recto .folio { right: 18px; }
</style>
</head>
<body>
<main class="canvas">

  <section class="spread spread--left">
    <article class="page page--verso">
      <svg class="halo" viewBox="0 0 263 380"><circle cx="131" cy="276" r="122" fill="var(--ring-grey)"/></svg>
      <div class="band-yellow"></div><div class="band-dark"></div>
      <svg class="medallion" viewBox="0 0 263 380"><path d="M9 284 A122 122 0 0 1 253 284 Z" fill="var(--yellow-light)" opacity=".5"/><path d="M9 284 A122 122 0 0 0 253 284 Z" fill="var(--charcoal-light)"/><circle cx="131" cy="276" r="78" fill="var(--yellow)"/><circle cx="131" cy="276" r="64" fill="#fff"/></svg>
      <div class="product-photo" role="img" aria-label="Product photo of a rental generator alternator"></div>
      <div class="gutter"></div>
      <header class="running-head"><span class="bar"></span><span class="section">OUR STOCK</span><span class="brand-mark"><i></i>Brightline Energy</span></header>
      <h1 class="title">RENTAL GENERATORS</h1>
      <h2 class="subtitle"><svg viewBox="0 0 10 10"><circle cx="5" cy="5" r="5" fill="var(--yellow)"/><path d="M4 3l2 2-2 2" stroke="#fff" stroke-width="1.4" fill="none"/></svg>RENTAL GENERATORS</h2>
      <p class="intro">Our generators are built for steady output across job sites, hospitals and plants. Each unit is tested before delivery, sized to your load and backed by local service teams who keep your power running day and night.</p>
      <ol class="points"><li><span>1</span>Fuel efficient engines with low noise and easy access panels.</li><li><span>2</span>Fast delivery and setup from our regional depots.</li><li><span>3</span>Full service plans and spare parts on hand.</li></ol>
      <footer class="folio"><span>8</span><span class="rule"></span><span>brightlineenergyco.example</span></footer>
    </article>
    <article class="page page--recto">
      <svg class="halo" viewBox="0 0 263 380"><circle cx="131" cy="276" r="122" fill="var(--ring-grey)"/></svg>
      <div class="band-yellow"></div><div class="band-dark"></div>
      <svg class="medallion" viewBox="0 0 263 380"><path d="M9 284 A122 122 0 0 1 253 284 Z" fill="var(--yellow-light)" opacity=".5"/><path d="M9 284 A122 122 0 0 0 253 284 Z" fill="var(--charcoal-light)"/><circle cx="131" cy="276" r="78" fill="var(--yellow)"/><circle cx="131" cy="276" r="64" fill="#fff"/></svg>
      <div class="product-photo" role="img" aria-label="Product photo of an AC alternator"></div>
      <div class="gutter"></div>
      <header class="running-head"><span class="brand-mark"><i></i>Brightline Energy</span><span class="section">OUR STOCK</span><span class="bar"></span></header>
      <h1 class="title">AC ALTERNATORS</h1>
      <h2 class="subtitle"><svg viewBox="0 0 10 10"><circle cx="5" cy="5" r="5" fill="var(--yellow)"/><path d="M4 3l2 2-2 2" stroke="#fff" stroke-width="1.4" fill="none"/></svg>AC ALTERNATORS</h2>
      <p class="intro">Our generators are built for steady output across job sites, hospitals and plants. Each unit is tested before delivery, sized to your load and backed by local service teams who keep your power running day and night.</p>
      <ol class="points"><li><span>1</span>Fuel efficient engines with low noise and easy access panels.</li><li><span>2</span>Fast delivery and setup from our regional depots.</li><li><span>3</span>Full service plans and spare parts on hand.</li></ol>
      <div class="feature-mark"><i></i>Brightline Energy</div>
      <footer class="folio"><span>brightlineenergyco.example</span><span class="rule"></span><span>9</span></footer>
    </article>
  </section>

  <section class="spread spread--right">
    <article class="page page--verso">
      <svg class="halo" viewBox="0 0 263 380"><circle cx="131" cy="276" r="122" fill="var(--ring-grey)"/></svg>
      <div class="band-yellow"></div><div class="band-dark"></div>
      <svg class="medallion" viewBox="0 0 263 380"><path d="M9 284 A122 122 0 0 1 253 284 Z" fill="var(--yellow-light)" opacity=".5"/><path d="M9 284 A122 122 0 0 0 253 284 Z" fill="var(--charcoal-light)"/><circle cx="131" cy="276" r="78" fill="var(--yellow)"/><circle cx="131" cy="276" r="64" fill="#fff"/></svg>
      <div class="product-photo" role="img" aria-label="Product photo of a standby generator voltage regulator board"></div>
      <div class="gutter"></div>
      <header class="running-head"><span class="bar"></span><span class="section">OUR STOCK</span><span class="brand-mark"><i></i>Brightline Energy</span></header>
      <h1 class="title">STANDBY GENERATORS</h1>
      <h2 class="subtitle"><svg viewBox="0 0 10 10"><circle cx="5" cy="5" r="5" fill="var(--yellow)"/><path d="M4 3l2 2-2 2" stroke="#fff" stroke-width="1.4" fill="none"/></svg>STANDBY GENERATORS</h2>
      <p class="intro">Our generators are built for steady output across job sites, hospitals and plants. Each unit is tested before delivery, sized to your load and backed by local service teams who keep your power running day and night.</p>
      <ol class="points"><li><span>1</span>Fuel efficient engines with low noise and easy access panels.</li><li><span>2</span>Fast delivery and setup from our regional depots.</li><li><span>3</span>Full service plans and spare parts on hand.</li></ol>
      <footer class="folio"><span>6</span><span class="rule"></span><span>brightlineenergyco.example</span></footer>
    </article>
    <article class="page page--recto">
      <svg class="halo" viewBox="0 0 263 380"><circle cx="131" cy="276" r="122" fill="var(--ring-grey)"/></svg>
      <div class="band-yellow"></div><div class="band-dark"></div>
      <svg class="medallion" viewBox="0 0 263 380"><path d="M9 284 A122 122 0 0 1 253 284 Z" fill="var(--yellow-light)" opacity=".5"/><path d="M9 284 A122 122 0 0 0 253 284 Z" fill="var(--charcoal-light)"/><circle cx="131" cy="276" r="78" fill="var(--yellow)"/><circle cx="131" cy="276" r="64" fill="#fff"/></svg>
      <div class="product-photo" role="img" aria-label="Product photo of a trailer-mounted prime generator"></div>
      <div class="gutter"></div>
      <header class="running-head"><span class="brand-mark"><i></i>Brightline Energy</span><span class="section">OUR STOCK</span><span class="bar"></span></header>
      <h1 class="title">PRIME GENERATORS</h1>
      <h2 class="subtitle"><svg viewBox="0 0 10 10"><circle cx="5" cy="5" r="5" fill="var(--yellow)"/><path d="M4 3l2 2-2 2" stroke="#fff" stroke-width="1.4" fill="none"/></svg>PRIME GENERATORS</h2>
      <p class="intro">Our generators are built for steady output across job sites, hospitals and plants. Each unit is tested before delivery, sized to your load and backed by local service teams who keep your power running day and night.</p>
      <ol class="points"><li><span>1</span>Fuel efficient engines with low noise and easy access panels.</li><li><span>2</span>Fast delivery and setup from our regional depots.</li><li><span>3</span>Full service plans and spare parts on hand.</li></ol>
      <div class="feature-mark"><i></i>Brightline Energy</div>
      <footer class="folio"><span>brightlineenergyco.example</span><span class="rule"></span><span>7</span></footer>
    </article>
  </section>

</main>
</body>
</html>
```